Luxury Wine Label for New Startup Winery

We need a wine label for our new winery startup. We have worked with a local designer but do not feel the resulting label / logo have the elevation required to present our brand as a luxury wine. Our winery is called "Quailbrook Vineyards" and we are focused on extremely high quality hand crafted artisan and estate wines from the Pacific Northwest.
We would like to see designs that utilize a tree line, or other imagery that represents the "Quailbrook" part of our company name. Another interesting feature could be wood grain.
A logo will be required based on your design so please design with this in mind:
This logo should be consistent with the wine bottle label design, and should be representative of our high end exclusive wine while giving a sense of place (Oregon/ Pacific Northwest.)
I will supply an image of the design we received from our local designer, PLEASE NOTE: in general we do like wood grain and tree line concepts but feel the execution was poorly done.
ATTN: Logo design should be suitable for use on: Bottles (Red wine/rose/white wine), Bussiness cards, vehicle signage, business signage, etc
P.S.:
If you have a design that is not outside the box we are still interested in seeing it.
Label is for a burgundy style bottle with a label height of 3.5 - 4" and a width of 3.5-4"
any label <= 4"x4" and >=3.5"x3.5" will be acceptable:
HOWEVER Width should be greater than or equal to height due to the bottle format
Target Market(s)
Wine enthusiasts with adequate discretionary budgets to afford $100 bottles of wine.
Industry/Entity Type
Wine / Winery
Requirements
Must have
- A sense of luxury, a feel of exclusivity, and a theme consistent with our product and brand name
Nice to have
- Tree line, wood grain or other wood themes. Serif fonts
Should not have
- anything cheesy, off topic, hard to read script fonts or anything that makes the label hard to read from a few feet away or too busy

```html
<!DOCTYPE html>
<html lang="en">
<head>
<meta charset="utf-8">
<title>Quailbrook Vineyards — Syrah Label</title>
<link rel="stylesheet" href="https://fonts.googleapis.com/css2?family=Cormorant+Garamond:wght@600;700&family=Josefin+Sans:wght@200&display=swap">
<style>
  :root {
    --canvas: #ecf0f1;
    --frame-silver: #b3b3b3;
    --label-black: #000000;
    --gold-deep: #c8b040;
    --gold-mid: #dccb7f;
    --gold-light: #f3ecd9;
    --wood-dark: #3a1d15;
    --wood-mid: #733924;
    --cream-line: #eadfca;
  }
  * { box-sizing: border-box; margin: 0; padding: 0; }
  html, body { width: 1200px; height: 1200px; overflow: hidden; }
  body { background: var(--canvas); position: relative; }

  .gold-text {
    background: linear-gradient(90deg, var(--gold-deep) 0%, var(--gold-mid) 25%, var(--gold-light) 50%, var(--gold-mid) 75%, var(--gold-deep) 100%);
    -webkit-background-clip: text;
    background-clip: text;
    color: transparent;
  }

  /* Brand label */
  .brand-label {
    position: absolute; left: 224px; top: 231px; width: 752px; height: 406px;
    background: var(--frame-silver); padding: 15px;
  }
  .brand-label__panel {
    position: relative; width: 100%; height: 100%; background: var(--label-black); overflow: hidden;
  }
  .treeline-area {
    position: absolute; left: 0; top: 0; width: 100%; height: 130px;
    background: linear-gradient(180deg, rgba(200,176,64,0.55) 0%, rgba(220,203,127,0.25) 55%, rgba(0,0,0,0) 100%);
  }
  .brand-name {
    position: absolute; left: 0; right: 0; top: 144px; text-align: center;
    font-family: "Cormorant Garamond", serif; font-weight: 700;
    font-size: 52px; line-height: 57px; letter-spacing: 0.18em;
    padding-left: 0.18em; text-transform: uppercase;
  }
  .brand-region {
    position: absolute; left: 0; right: 0; top: 278px; text-align: center;
    font-family: "Cormorant Garamond", serif; font-weight: 700;
    font-size: 25px; letter-spacing: 0.32em; padding-left: 0.32em; text-transform: uppercase;
  }
  .brand-name span, .brand-region span { display: inline-block; }

  /* Varietal label */
  .varietal-label {
    position: absolute; left: 224px; top: 709px; width: 752px; height: 260px;
    background: linear-gradient(100deg, var(--gold-deep) 0%, var(--gold-mid) 25%, var(--gold-light) 50%, var(--gold-mid) 75%, var(--gold-deep) 100%);
    padding: 16px;
  }
  .varietal-label__panel {
    position: relative; width: 100%; height: 100%; overflow: hidden;
  }
  .woodgrain-area {
    position: absolute; inset: 0;
    background: linear-gradient(180deg, var(--wood-mid) 0%, #5a2c1d 50%, var(--wood-dark) 100%);
  }
  .varietal-name {
    position: absolute; left: 0; right: 0; top: 6px; text-align: center;
    font-family: "Cormorant Garamond", serif; font-weight: 600;
    font-size: 148px; line-height: 170px; font-variant: small-caps; letter-spacing: 0.01em;
  }
  .varietal-name span { display: inline-block; }
  .varietal-meta {
    position: absolute; left: 0; right: 0; top: 166px; text-align: center;
    font-family: "Josefin Sans", sans-serif; font-weight: 200;
    font-size: 19px; letter-spacing: 0.42em; padding-left: 0.42em; color: var(--cream-line);
  }
</style>
</head>
<body>
  <section class="brand-label">
    <div class="brand-label__panel">
      <div class="treeline-area" role="img" aria-label="Gold forest tree line illustration across the top of the label"></div>
      <h1 class="brand-name"><span class="gold-text">Quailbrook</span><br><span class="gold-text">Vineyards</span></h1>
      <p class="brand-region"><span class="gold-text">Willamette Valley</span></p>
    </div>
  </section>

  <section class="varietal-label">
    <div class="varietal-label__panel">
      <div class="woodgrain-area" role="img" aria-label="Dark walnut wood grain texture"></div>
      <h2 class="varietal-name"><span class="gold-text">Syrah</span></h2>
      <p class="varietal-meta">ESTATE | 2023 | GROWN</p>
    </div>
  </section>
</body>
</html>
```